Healthy Food Healthy Brain Rack Card

We want a new 2 page (front and page) 3.67" x 8.5" rack card. This rack card is the first of a series we are creating. We will have five more eventually.

The minimum font size for the text on the front is 11 point and also for other main body text.

Use the text on the word document.

The images and layout in the word document are just sample ideas we had.

We have a subscripton to plivora pics images so prefer to get images from there or free high quality images.

The document is for older readers. Do not put text over graphics and keep it simple and easy to read with high contrast.

We are open to any color scheme, though something that conveys fresh and healthy, is good.

We want some very simple design element(s) incorporated that convey Native American communities or heritage. But NO head dress, teepee graphics, etc.

At the top, of the first page we would like a collage of healthy food images. This can include fish, chicken, fresh vegetables, berries, brown rice, etc.

On the back side, the text below the brown box on the word document with the title "mock up" can be smaller as needed.

Please remember to include the funding statement - it can be in a very small font 6/7 point.

For more information about our project, please visit https://veltronaq.org/mind-care/

```html
<!DOCTYPE html>
<html lang="en">
<head>
<meta charset="utf-8">
<title>Healthy Food Healthy Brain Rack Card</title>
<link rel="stylesheet" href="https://fonts.googleapis.com/css2?family=Montserrat:wght@800&family=Fira+Sans:ital,wght@0,400;0,600;1,600&display=swap">
<style>
:root{
  --bg:#f4f4f4;
  --berry:#971b2f;
  --teal:#5ba4b1;
  --ink:#1e1e1e;
  --white:#ffffff;
}
*{margin:0;padding:0;box-sizing:border-box}
html,body{width:1200px;height:1200px;overflow:hidden;background:var(--bg)}
body{position:relative;font-family:"Fira Sans",sans-serif;color:var(--ink)}
.card{position:absolute;top:75px;width:461px;height:1068px;background:var(--white);box-shadow:0 2px 8px rgba(0,0,0,.18);overflow:hidden}
.card--front{left:111px}
.card--back{left:607px}

/* front */
.collage{position:absolute;left:0;top:0;width:461px;height:135px;display:grid;grid-template-columns:1fr 1fr;grid-template-rows:1fr 1fr}
.collage__tile{display:block}
.tile-protein{background:linear-gradient(135deg,#e9e2dc,#c98a86 55%,#d9d2cc)}
.tile-greens{background:linear-gradient(135deg,#6b8f3a,#e8dcc8 50%,#4d7a2e)}
.tile-citrus{background:linear-gradient(135deg,#8fb05a,#f06a4a 45%,#f2e4cc)}
.tile-roots{background:linear-gradient(135deg,#a88a66,#d8402e 50%,#c9a26a)}
.front-title{position:absolute;left:0;top:155px;width:461px;text-align:center;font-family:"Montserrat",sans-serif;font-weight:800;font-size:51px;line-height:52px;color:var(--berry);letter-spacing:-.5px}
.front-intro{position:absolute;left:24px;top:268px;width:413px;text-align:center;font-style:italic;font-weight:600;font-size:18.6px;line-height:24.5px;color:var(--berry)}
.steps{position:absolute;left:5px;top:416px;width:450px;height:461px;background:var(--berry);color:var(--white);padding:24px 20px 0 25px}
.steps__heading{font-weight:600;font-size:17.5px;margin-bottom:20px}
.steps__list{list-style:none;font-size:17px;line-height:28px}
.steps__list li{padding-left:14px;text-indent:-14px}
.steps__list li::before{content:"•";display:inline-block;width:14px;text-indent:0}
.steps__note{margin-top:18px;font-weight:600;font-size:18px;line-height:28px}
.doctor{position:absolute;left:0;top:892px;width:461px;text-align:center;font-weight:600;font-size:18.4px;line-height:24.5px;text-transform:uppercase}
.quote{position:absolute;left:5px;top:953px;width:450px;height:108px;background:var(--berry);color:var(--white);text-align:center;font-style:italic;font-weight:600;font-size:18.8px;line-height:28px;padding-top:12px}

/* back */
.back-header{position:absolute;left:0;top:0;width:461px;height:98px;background:var(--berry);color:var(--white);font-weight:600;font-size:43px;text-align:center;line-height:98px;letter-spacing:-.3px}
.recipe-photo{position:absolute;left:34px;top:118px;width:176px;height:178px;background:linear-gradient(135deg,#cfd3d8,#e98a6e 55%,#9fb86a)}
.recipe-name{position:absolute;left:34px;top:296px;width:176px;height:56px;background:var(--berry);color:var(--white);text-align:center;font-weight:600;font-size:17px;line-height:21px;padding-top:7px}
.ingredients{position:absolute;left:221px;top:114px;font-size:17px;line-height:21.8px}
.ingredients__title{font-weight:600}
.method{position:absolute;left:0;top:372px;width:461px;height:213px;background:var(--berry);color:var(--white);text-align:center;font-size:17px;line-height:22.7px;padding:15px 16px 0}
.community{position:absolute;left:0;top:585px;width:461px;height:171px;background:var(--teal);color:var(--white);text-align:center;font-style:italic;font-weight:600;font-size:22px;line-height:28px;padding-top:14px}
.resources{position:absolute;left:0;top:756px;width:461px;height:233px;font-size:12.5px}
.res-heading{font-weight:600;font-size:16px}
.res-left{position:absolute;left:17px;top:15px}
.res-right{position:absolute;right:19px;top:15px;text-align:right}
.res-sub{font-weight:600;margin-top:5px;line-height:14px}
.res-url{line-height:14px}
.res-center{position:absolute;left:0;top:108px;width:461px;text-align:center;line-height:14px}
.brand{position:absolute;left:80px;top:166px;display:flex;align-items:center;gap:14px}
.brand__mark{width:76px;height:76px;border-radius:50%;background:var(--teal)}
.brand__name{font-weight:600;font-size:18px;line-height:21px;color:var(--teal);width:210px}
.funding{position:absolute;left:0;top:989px;width:461px;height:79px;background:var(--teal);color:var(--white);font-size:9.4px;line-height:14px;padding:11px 17px 0}
</style>
</head>
<body>

<section class="card card--front">
  <div class="collage">
    <span class="collage__tile tile-protein" role="img" aria-label="Photo of fresh fish, meat and poultry"></span>
    <span class="collage__tile tile-greens" role="img" aria-label="Photo of fresh vegetables and fruit"></span>
    <span class="collage__tile tile-citrus" role="img" aria-label="Photo of grapefruit, apple and broccoli"></span>
    <span class="collage__tile tile-roots" role="img" aria-label="Photo of ginger, tomatoes and produce"></span>
  </div>
  <h1 class="front-title">HEALTHY FOOD<br>HEALTHY BRAIN</h1>
  <p class="front-intro">Everyone slows down as they get older, both in body and mind. Eating healthier food can help your overall health, including brain health. It may also reduce your risk for memory loss and problems thinking.</p>
  <div class="steps">
    <h2 class="steps__heading">Healthier steps to protect your brain:</h2>
    <ul class="steps__list">
      <li>Eat more vegetables, fruits, whole grains, and lower-fat milk</li>
      <li>Use less salt and added sugar</li>
      <li>Eat more fish, chicken, turkey, beans, and nuts</li>
      <li>Cut down on bad fats (“saturated” and trans), cholesterol, and red meat</li>
      <li>Buy fresh, not packaged food when you can</li>
      <li>Limit how much alcohol you drink</li>
      <li>Learn your daily calorie needs for your body size</li>
      <li>Take care of your mental and spiritual health to support your physical and brain health</li>
    </ul>
    <p class="steps__note">Small changes can make a big difference for better brain health.</p>
  </div>
  <p class="doctor">Talk to your doctor about more steps<br>to healthier food choices.</p>
  <blockquote class="quote">“Without the elk, salmon, huckleberries,<br>shellfish, and cedar trees we are nobody…”<br>Mara Tolweya (Kessik River)</blockquote>
</section>

<section class="card card--back">
  <h2 class="back-header">Make This at Home</h2>
  <div class="recipe-photo" role="img" aria-label="Photo of salmon and vegetables in a foil packet"></div>
  <p class="recipe-name">Grilled Salmon and Veggie Foil Packets</p>
  <div class="ingredients">
    <p class="ingredients__title">Ingredients:</p>
    <p>Salmon<br>Asparagus<br>Red or Green Peppers<br>(Or any seasonal vegetable)<br>Onion<br>Lemon – sliced<br>Basil<br>Olive Oil<br>Salt and Pepper<br>Garlic Powder</p>
  </div>
  <p class="method">Cut asparagus, peppers, and onion into bite-size pieces. Cut salmon into 4-6 oz pieces. Tear tin foil large enough to wrap around salmon &amp; veggies (2 layers). Add veggies and salmon to foil. Drizzle with olive oil, season with salt, pepper, basil, garlic &amp; top with a piece of sliced lemon. Wrap foil tightly around food. Grill at 400 degrees for about 20 minutes. Careful opening!</p>
  <p class="community">Food &amp; drink are a source of strength<br>and connection to community. A return<br>to traditional food pathways and eating<br>local, seasonal fresh foods make<br>healthier eating easier.</p>
  <div class="resources">
    <div class="res-left">
      <p class="res-heading">For More Information</p>
      <p class="res-sub">About Healthier Eating</p>
      <p class="res-sub" style="margin-top:8px">BalancedTable</p>
      <p class="res-url">https://www.balancedtable.org</p>
    </div>
    <div class="res-right">
      <p class="res-heading">About Brain Health</p>
      <p class="res-sub">Northern Roots Center for<br>Native Brain Health</p>
      <p class="res-url">https://www.northernrootsbrain.org</p>
    </div>
    <div class="res-center">
      <p style="font-weight:600">Healthy Aging Memory Program</p>
      <p>https://www.healthyagingmemory.org</p>
    </div>
    <div class="brand">
      <span class="brand__mark"></span>
      <span class="brand__name">NORTHERN ROOTS BRAIN HEALTH CENTER</span>
    </div>
  </div>
  <p class="funding">This product is supported by the National Wellness Agency (NWA) of the Federal Health Department (FHD) as part of a financial assistance award totaling $348,711 with 100 percent funded by NWA/FHD. The contents are those of the author(s) and do not necessarily represent the official views of, nor an endorsement, by NWA/FHD.</p>
</section>

</body>
</html>
```